Furniture & Lighting Wholesaler Needs a Product Catalogue/Look Book

Our company, Vostre Merchant Co, imports quality hand-made furniture, lighting and decor from South Africa. Our products are well-designed and are designed to be used in up-market hotels and homes. Our primary customers are small- to medium-size retail shops.
We require a +/- 14-16 page look book (concept as per attached image) that will be used both in hard-copy and online. We have all of the necessary high-res images, descriptions/text etc. We need you to propose several design concepts from which we can choose, and then execute the design.
Please visit our website www.vostremerchant.example to see the products and their descriptions, as well as to get a feel for our style. Thank you for looking at our project!
Target Market(s)
Boutique Furniture Stores; Interior Designers
Industry/Entity Type
It Company
Font styles to use
Other font styles liked:
- Bauer Bodini and Open Sans Condensed
Look and feel
Each slider illustrates characteristics of the customer's brand and the style your logo design should communicate.

```html
<!DOCTYPE html>
<html lang="en">
<head>
<meta charset="utf-8">
<title>Vostre Merchant Co – Look Book Spread</title>
<link rel="stylesheet" href="https://fonts.googleapis.com/css2?family=Open+Sans:wght@300;400;600;700&display=swap">
<style>
  :root{
    --bg:#d8d8d8;
    --paper:#f7f7f5;
    --gold:#ab9b6d;
    --gold-dark:#8f7f52;
    --ink:#3a3a3a;
    --muted:#6d6d6d;
    --rule:#d6d6d2;
    --tab:#4a4a4a;
    --tile-a:#6f716c;
    --tile-b:#2f312e;
  }
  *{box-sizing:border-box;margin:0;padding:0}
  html,body{width:1200px;height:800px;overflow:hidden}
  body{background:var(--bg);font-family:"Open Sans",sans-serif;color:var(--ink);position:relative}

  .spread{position:absolute;left:20px;top:195px;width:1160px;height:410px;display:flex;box-shadow:0 10px 30px rgba(0,0,0,.18)}
  .page{position:relative;width:580px;height:410px;background:var(--paper);overflow:hidden}
  .page--left{background:linear-gradient(90deg,var(--paper) 88%,#e9e9e6 100%)}
  .page--right{background:linear-gradient(90deg,#e9e9e6 0%,var(--paper) 10%)}

  /* edge bands */
  .edge-band{position:absolute;width:24px;background:var(--gold)}
  .page--left .edge-band{left:0;top:205px;bottom:0;border-top-right-radius:22px}
  .page--right .edge-band{right:0;top:0;height:190px;border-bottom-left-radius:22px}
  .page-number{position:absolute;width:34px;height:30px;background:var(--tab);color:var(--gold);font-size:10px;display:flex;align-items:center;justify-content:center}
  .page--left .page-number{left:0;bottom:0;border-top-right-radius:14px}
  .page--right .page-number{right:0;top:160px;border-top-left-radius:14px;border-bottom-left-radius:14px}

  /* footer */
  .page-footer{position:absolute;bottom:12px;display:flex;align-items:center;gap:6px;background:#e6e6e3;border-radius:10px;padding:3px 12px;font-size:6.5px;color:var(--muted)}
  .page--left .page-footer{right:30px}
  .page--right .page-footer{left:30px}
  .page-footer .mark{width:8px;height:8px;border:1.5px solid var(--ink)}

  /* product tile */
  .tile{border:2px solid var(--gold);border-radius:12px;background:#fff;padding:6px;box-shadow:2px 3px 4px rgba(0,0,0,.12)}
  .tile .photo{width:100%;height:100%;border-radius:6px;background:radial-gradient(circle at 50% 40%,var(--tile-a),var(--tile-b) 70%,#fff 72%)}

  .product-name{color:var(--gold);text-transform:uppercase;font-weight:400;letter-spacing:.02em}
  .product-desc{font-weight:600;color:var(--ink)}
  .price{background:var(--gold);color:#fff;display:inline-flex;align-items:center;justify-content:center;box-shadow:2px 2px 0 var(--gold-dark)}
  .features{list-style:none;color:var(--muted)}
  .features li::before{content:"•";margin-right:4px;color:var(--ink)}

  /* left page list */
  .catalogue--large{position:absolute;left:48px;top:28px;right:26px;display:flex;flex-direction:column;gap:12px}
  .item--large{display:grid;grid-template-columns:78px 180px 92px 1fr;align-items:center;column-gap:12px;height:76px;position:relative}
  .item--large::after{content:"";position:absolute;left:90px;right:0;top:-7px;border-top:1px solid var(--rule)}
  .item--large:first-child::after{display:none}
  .item--large .tile{width:76px;height:76px}
  .item--large .product-name{font-size:10px}
  .item--large .product-desc{font-size:7.5px;line-height:1.3;margin-top:2px}
  .item--large .price{width:80px;height:26px;font-size:13px}
  .item--large .features{font-size:7px;line-height:1.45}

  /* right page grid */
  .catalogue--small{position:absolute;left:30px;top:26px;right:40px;display:grid;grid-template-columns:1fr 1fr;column-gap:16px;row-gap:12px}
  .item--small{display:grid;grid-template-columns:60px 108px 1fr;align-items:center;column-gap:8px;height:76px;position:relative}
  .item--small::after{content:"";position:absolute;left:66px;right:0;bottom:-7px;border-top:1px solid var(--rule)}
  .item--small .tile{width:60px;height:60px;padding:5px;border-radius:10px}
  .item--small .product-name{font-size:8.5px}
  .item--small .product-desc{font-size:5.5px;margin-top:1px}
  .item--small .price{width:46px;height:16px;font-size:7px;margin-top:6px}
  .item--small .features{font-size:4.8px;line-height:1.5}
</style>
</head>
<body>
<main class="spread">
  <section class="page page--left">
    <div class="edge-band"></div>
    <div class="page-number">12</div>
    <div class="catalogue--large">
      <article class="item--large">
        <div class="tile"><div class="photo" role="img" aria-label="Black upholstered armchair product photo"></div></div>
        <div><h3 class="product-name">Product Name</h3><p class="product-desc">Faccuipa ipilm excearum rae expligent lam qui occulpa rchicle ndesequ latur Tature dit derionti la dolesec aboruptur</p></div>
        <div class="price">$59.99</div>
        <ul class="features"><li>Sint labor simelluptat ullen empellacit</li><li>Es maximus si num ad etus</li><li>Acersped moluptaquate</li><li>Pitaqui dipiciet que sit dolor</li></ul>
      </article>
      <article class="item--large">
        <div class="tile"><div class="photo" role="img" aria-label="Black upholstered armchair product photo"></div></div>
        <div><h3 class="product-name">Product Name</h3><p class="product-desc">Faccuipa ipilm excearum rae expligent lam qui occulpa rchicle ndesequ latur Tature dit derionti la dolesec aboruptur</p></div>
        <div class="price">$59.99</div>
        <ul class="features"><li>Sint labor simelluptat ullen empellacit</li><li>Es maximus si num ad etus</li><li>Acersped moluptaquate</li><li>Pitaqui dipiciet que sit dolor</li></ul>
      </article>
      <article class="item--large">
        <div class="tile"><div class="photo" role="img" aria-label="Black upholstered armchair product photo"></div></div>
        <div><h3 class="product-name">Product Name</h3><p class="product-desc">Faccuipa ipilm excearum rae expligent lam qui occulpa rchicle ndesequ latur Tature dit derionti la dolesec aboruptur</p></div>
        <div class="price">$59.99</div>
        <ul class="features"><li>Sint labor simelluptat ullen empellacit</li><li>Es maximus si num ad etus</li><li>Acersped moluptaquate</li><li>Pitaqui dipiciet que sit dolor</li></ul>
      </article>
      <article class="item--large">
        <div class="tile"><div class="photo" role="img" aria-label="Black upholstered armchair product photo"></div></div>
        <div><h3 class="product-name">Product Name</h3><p class="product-desc">Faccuipa ipilm excearum rae expligent lam qui occulpa rchicle ndesequ latur Tature dit derionti la dolesec aboruptur</p></div>
        <div class="price">$59.99</div>
        <ul class="features"><li>Sint labor simelluptat ullen empellacit</li><li>Es maximus si num ad etus</li><li>Acersped moluptaquate</li><li>Pitaqui dipiciet que sit dolor</li></ul>
      </article>
    </div>
    <footer class="page-footer"><span class="mark"></span>www.vostremerchant.example</footer>
  </section>

  <section class="page page--right">
    <div class="edge-band"></div>
    <div class="page-number">13</div>
    <div class="catalogue--small">
      <article class="item--small"><div class="tile"><div class="photo" role="img" aria-label="Black upholstered armchair product photo"></div></div><div><h3 class="product-name">Product Name</h3><p class="product-desc">Faccuipa ipilm excearum rae expligent.</p><div class="price">$59.99</div></div><ul class="features"><li>Sint labor simel ullam</li><li>Es maximus si num</li><li>Acersped molupta quate</li><li>Pitaqui dipiciet que</li></ul></article>
      <article class="item--small"><div class="tile"><div class="photo" role="img" aria-label="Black upholstered armchair product photo"></div></div><div><h3 class="product-name">Product Name</h3><p class="product-desc">Faccuipa ipilm excearum rae expligent.</p><div class="price">$59.99</div></div><ul class="features"><li>Sint labor simel ullam</li><li>Es maximus si num</li><li>Acersped molupta quate</li><li>Pitaqui dipiciet que</li></ul></article>
      <article class="item--small"><div class="tile"><div class="photo" role="img" aria-label="Black upholstered armchair product photo"></div></div><div><h3 class="product-name">Product Name</h3><p class="product-desc">Faccuipa ipilm excearum rae expligent.</p><div class="price">$59.99</div></div><ul class="features"><li>Sint labor simel ullam</li><li>Es maximus si num</li><li>Acersped molupta quate</li><li>Pitaqui dipiciet que</li></ul></article>
      <article class="item--small"><div class="tile"><div class="photo" role="img" aria-label="Black upholstered armchair product photo"></div></div><div><h3 class="product-name">Product Name</h3><p class="product-desc">Faccuipa ipilm excearum rae expligent.</p><div class="price">$59.99</div></div><ul class="features"><li>Sint labor simel ullam</li><li>Es maximus si num</li><li>Acersped molupta quate</li><li>Pitaqui dipiciet que</li></ul></article>
      <article class="item--small"><div class="tile"><div class="photo" role="img" aria-label="Black upholstered armchair product photo"></div></div><div><h3 class="product-name">Product Name</h3><p class="product-desc">Faccuipa ipilm excearum rae expligent.</p><div class="price">$59.99</div></div><ul class="features"><li>Sint labor simel ullam</li><li>Es maximus si num</li><li>Acersped molupta quate</li><li>Pitaqui dipiciet que</li></ul></article>
      <article class="item--small"><div class="tile"><div class="photo" role="img" aria-label="Black upholstered armchair product photo"></div></div><div><h3 class="product-name">Product Name</h3><p class="product-desc">Faccuipa ipilm excearum rae expligent.</p><div class="price">$59.99</div></div><ul class="features"><li>Sint labor simel ullam</li><li>Es maximus si num</li><li>Acersped molupta quate</li><li>Pitaqui dipiciet que</li></ul></article>
      <article class="item--small"><div class="tile"><div class="photo" role="img" aria-label="Black upholstered armchair product photo"></div></div><div><h3 class="product-name">Product Name</h3><p class="product-desc">Faccuipa ipilm excearum rae expligent.</p><div class="price">$59.99</div></div><ul class="features"><li>Sint labor simel ullam</li><li>Es maximus si num</li><li>Acersped molupta quate</li><li>Pitaqui dipiciet que</li></ul></article>
      <article class="item--small"><div class="tile"><div class="photo" role="img" aria-label="Black upholstered armchair product photo"></div></div><div><h3 class="product-name">Product Name</h3><p class="product-desc">Faccuipa ipilm excearum rae expligent.</p><div class="price">$59.99</div></div><ul class="features"><li>Sint labor simel ullam</li><li>Es maximus si num</li><li>Acersped molupta quate</li><li>Pitaqui dipiciet que</li></ul></article>
    </div>
    <footer class="page-footer"><span class="mark"></span>www.vostremerchant.example</footer>
  </section>
</main>
</body>
</html>
```